Request for Business Card Design

Hi. My name is Marlene, I am looking for a new business card design for my company, Quarrow Signal Instruments, LLC. I really like the design you did for Tarsel Venture and was hoping you could do something similar using our full logo and our mark. I am also open to any raised texture design using our mark. I have attached our full logo, which would need to be somewhere on the card, as well as the mark in both outline and full form, as well as our brand colors / guide. The card does not have to be white, as long as our logo and mark appear. I actually like darker colored business cards more, but am open to all options. If you are interested in working with me, please let me know. We would also take the business card design into letterhead design if you can do that.

```html
<!DOCTYPE html>
<html lang="en">
<head>
<meta charset="utf-8">
<title>Quarrow Signal Instruments — Business Card</title>
<link rel="stylesheet" href="https://fonts.googleapis.com/css2?family=Barlow:wght@400;500;600&family=Montserrat:wght@400;700&display=swap">
<style>
  :root {
    --bg-light: #eeeeee;
    --bg-dark: #9a9a9a;
    --card-top: #5e5e60;
    --card-mid: #3f3f41;
    --card-deep: #242122;
    --band: #4a4a4c;
    --ink: #ffffff;
    --ink-soft: #e9e9e9;
    --accent-light: #ebebeb;
    --accent-ring: #3a3a3c;
  }
  * { margin: 0; padding: 0; box-sizing: border-box; }
  html, body { width: 1200px; height: 1200px; overflow: hidden; }
  body {
    background: linear-gradient(120deg, var(--bg-light) 0%, #cfcfcf 55%, var(--bg-dark) 100%);
    font-family: "Barlow", sans-serif;
    position: relative;
  }
  .card {
    position: absolute;
    left: 180px;
    width: 840px;
    height: 480px;
    border-radius: 30px;
    overflow: hidden;
    box-shadow: 0 6px 0 #1a1a1a, 0 16px 30px rgba(0,0,0,0.25);
  }
  .card--front {
    top: 80px;
    background: linear-gradient(115deg, var(--card-top) 0%, var(--card-mid) 60%, #353537 100%);
  }
  .card--back {
    top: 630px;
    background: linear-gradient(100deg, #3c3a3b 0%, var(--card-deep) 60%, #2b2a2b 100%);
  }

  /* brand lockup */
  .brand { position: absolute; display: flex; align-items: center; color: var(--ink); font-weight: 600; }
  .brand__dot { border-radius: 50%; background: var(--ink); flex: none; }
  .brand__name { display: flex; flex-direction: column; line-height: 1; text-transform: uppercase; }
  .brand__word { letter-spacing: 0.12em; }

  .card--front .brand { left: 150px; top: 172px; gap: 34px; }
  .card--front .brand__dot { width: 110px; height: 110px; }
  .card--front .brand__word--main { font-size: 92px; }
  .card--front .brand__word--sub { font-size: 25px; letter-spacing: 0.1em; margin-top: 6px; }

  /* back */
  .back__band {
    position: absolute; left: 0; top: 0; width: 100%; height: 190px;
    background: linear-gradient(100deg, #606062 0%, var(--band) 55%, #3d3d3f 100%);
  }
  .card--back .brand { left: 70px; top: 62px; gap: 20px; }
  .card--back .brand__dot { width: 58px; height: 58px; }
  .card--back .brand__word--main { font-size: 46px; }
  .card--back .brand__word--sub { font-size: 13px; letter-spacing: 0.1em; margin-top: 4px; }

  .person { position: absolute; right: 130px; top: 40px; text-align: right; color: var(--ink); }
  .person__name { font-family: "Montserrat", sans-serif; font-weight: 700; font-size: 34px; }
  .person__title { font-family: "Montserrat", sans-serif; font-weight: 400; font-size: 19px; margin-top: 6px; color: var(--ink-soft); }

  .back__tab {
    position: absolute; right: -14px; top: 36px; width: 40px; height: 64px;
    border-radius: 12px; background: var(--accent-light);
  }
  .back__mark { position: absolute; right: -120px; top: 160px; width: 420px; height: 420px; }

  .contact { position: absolute; left: 90px; top: 230px; color: var(--ink); }
  .contact__address { font-size: 24px; line-height: 1.3; letter-spacing: 0.04em; margin-bottom: 16px; }
  .contact__list { list-style: none; }
  .contact__item { display: flex; align-items: center; gap: 16px; font-size: 24px; letter-spacing: 0.05em; line-height: 1.32; }
  .contact__icon { width: 18px; height: 18px; flex: none; fill: var(--ink); }
</style>
</head>
<body>

<section class="card card--front" aria-label="Card front">
  <div class="brand">
    <span class="brand__dot"></span>
    <span class="brand__name">
      <span class="brand__word brand__word--main">Quarrow</span>
      <span class="brand__word brand__word--sub">Signal Instruments</span>
    </span>
  </div>
</section>

<section class="card card--back" aria-label="Card back">
  <div class="back__band"></div>
  <svg class="back__mark" viewBox="0 0 420 420" aria-hidden="true">
    <circle cx="210" cy="210" r="200" fill="#ebebeb"/>
  </svg>
  <div class="back__tab"></div>

  <div class="brand">
    <span class="brand__dot"></span>
    <span class="brand__name">
      <span class="brand__word brand__word--main">Quarrow</span>
      <span class="brand__word brand__word--sub">Signal Instruments</span>
    </span>
  </div>

  <div class="person">
    <p class="person__name">Marlene</p>
    <p class="person__title">Founder &amp; Director</p>
  </div>

  <div class="contact">
    <p class="contact__address">1870 Harrow Field Road.<br>Brackenford, CO 80761</p>
    <ul class="contact__list">
      <li class="contact__item">
        <svg class="contact__icon" viewBox="0 0 24 24"><path d="M6.6 10.8a15 15 0 0 0 6.6 6.6l2.2-2.2c.3-.3.7-.4 1-.2 1.1.4 2.3.6 3.6.6.6 0 1 .4 1 1V20c0 .6-.4 1-1 1A17 17 0 0 1 3 4c0-.6.4-1 1-1h3.5c.6 0 1 .4 1 1 0 1.3.2 2.5.6 3.6.1.3 0 .7-.2 1z"/></svg>
        +001 555 218 4407
      </li>
      <li class="contact__item">
        <svg class="contact__icon" viewBox="0 0 24 24"><path d="M6 2h12v6H6zM4 9h16a2 2 0 0 1 2 2v6h-4v5H6v-5H2v-6a2 2 0 0 1 2-2zm4 8v3h8v-3z"/></svg>
        +001 555 218 4412
      </li>
      <li class="contact__item">
        <svg class="contact__icon" viewBox="0 0 24 24"><path d="M2 5h20v14H2zm2 2v.5l8 5 8-5V7z"/></svg>
        hello@quarrowsignal.com
      </li>
      <li class="contact__item">
        <svg class="contact__icon" viewBox="0 0 24 24"><path d="M12 2a10 10 0 1 0 0 20 10 10 0 0 0 0-20zm-1 2.1V11H4.1A8 8 0 0 1 11 4.1zm2 0a8 8 0 0 1 6.9 6.9H13zM4.1 13H11v6.9A8 8 0 0 1 4.1 13zm8.9 6.9V13h6.9a8 8 0 0 1-6.9 6.9z"/></svg>
        www.quarrowsignal.com
      </li>
    </ul>
  </div>
</section>

</body>
</html>
```